Wordpress Theme for Medical Clinics

** Please view updated Sitemap2.pdf doc to clarify some confusion ***

This is a multiuser WordPress subscription site for medical clinics. Please see attachment for sitemap. Please do not include extra content like social media icons, search bars, or images. If you have questions, please ask for clarification.
The site contains the following pages and sub-pages:

1. Home
2. Our Clinic
2a. Our Clinic > Mission
2b. Our Clinic > Services
2c. Our Clinic > Clinic Policies
2d. Our Clinic > Schedules
3. Our Staff
3a. Our Staff > [Staff member page]
4. Resources
4a. Resources > Patient Health (index)
4b. Resources > Patient Health (index) > [post]
4c. Resources > Links
4d. Resources > Forms
5. Alerts
5a. Alerts > [Alert Page]
6. Contact Us

Includes the Following Pages, Subpages, and Content
1. Home
a. About Us
b. Our Staff
c. Bulletins
d. Accepting New Patients (shown as an alert widget)
e. Links
i. Physician Toolbox
ii. Book an Appointment
f. Clinic Policies
i. Show first 3 policies (e.g. Late Arrivals, Missed Appointments, Fees)
ii. Link to Clinic Policies page
g. Primary widget (displayed on all pages)
i. Hours of operation
ii. Contact Info
1. Tel
2. Fax
3. Email
4. Address
5. Get directions (link to Google Maps)
2. Our Clinic
a. Main Page
i. Clinic Name
ii. Overview
iii. Languages Spoken
iv. Secondary Navigation
1. Mission
2. Services
3. Clinic Policies
4. Schedules (see attachment)
b. Our Clinic > Mission
c. Our Clinic > Services
i. For each service include service TITLE and DESCRIPTION
d. Our Clinic > Clinic Policies
i. For each policy include policy TITLE and DESCRIPTION
ii. Include the following policies in mockup
1. Late arrivals
2. Missed appointments
3. Fees for missed appointments
4. Referrals and follow-ups
5. Services not covered by RDA
6. Information for LTF patients
7. Medical Legal Reports
e. Our Clinic > Schedules
3. Our Staff
a. Main Page
i. Display a list of staff members. Include NAME and DESIGNATION
b. Our Staff > [Staff Name]
i. Include NAME, PICTURE, DESIGNATION, and BIO
4. Resources
a. Resources > Patient Health
i. Main Page
1. Posts (ordered by date)
a. Title
b. Summary
2. Side Navigation
a. Post Categories
ii. Patient Health > [post title]
1. Title
2. Post Category
3. Date
4. Author
5. Summary
6. Body
b. Resources > Links
1. Secondary Navigation - Categories
a. Sample Categories:
i. Local Services
ii. RDA and Drug Coverage
iii. Mental Health Resources
2. Category page
a. Include the following links in the 'Local Services' category
i. Hypertension clinics
ii. Home Care services
iii. Vaccine Clinics
c. Resources > Forms
i. Display a table with form TITLE and CATEGORY
ii. Side Navigation
1. Form Categories
a. Use the following sample Categories
i. Referrals
ii. Insurance
iii. Intake
iv. Discharge
v. Waivers
5. Alerts
a. Main page
i. List of all Alert posts
1. Include post TITLE as a link to the post
ii. Side Navigation
1. Alerts Archive
a. shown as Month + Number of posts
iii. Alerts > [Alert page]
1. Include TITLE, DATE, AUTHOR, BODY
6. Contact Us
a. Map
b. Hours of operation
c. Address
d. Phone number
e. Fax number
e. Fax number
f. Map
g. Email

Design notes:
- fixed width
- responsive (need designs for mobile, tablet, and desktop)
- simple, dark font, white background
- use Font Awesome icons where needed
- user adds own logo

Target Market(s)

Medical Clinics

Industry/Entity Type

Medical

Number of Pages Required

5+ page

Font styles to use
Serif
Sans Serif

Requirements
Must have
• Please keep designs very simple.
• Examples:
• https://www.quolbin.com/install
• http://www.ventrohax.com/company/about-us
• http://brindlequota.org/
• http://www.trosk.com/
Should not have
• Minimal or no use of shadows and gradients

```html
<!DOCTYPE html>
<html lang="en">
<head>
<meta charset="utf-8">
<title>Medical Clinics – Resources</title>
<link href="https://fonts.googleapis.com/css2?family=Open+Sans:wght@400;600;700&family=Raleway:wght@500;600&display=swap" rel="stylesheet">
<style>
:root{
  --blue:#0a8be2;
  --blue-dark:#0877cc;
  --ink:#222;
  --text:#333;
  --muted:#555;
  --rule:#dcdcdc;
  --band:#f7f7f7;
  --footer:#262626;
  --footer-text:#8a8a8a;
  --footer-head:#9a9a9a;
  --white:#fff;
}
*{box-sizing:border-box;margin:0;padding:0}
html,body{width:1200px;height:1035px;overflow:hidden}
body{position:relative;font-family:"Open Sans",Arial,sans-serif;color:var(--text);background:var(--white)}
.abs{position:absolute}
a{color:inherit;text-decoration:none}

.topbar{left:0;top:0;width:1200px;height:30px;background:var(--blue);color:var(--white);font-size:10px;line-height:30px}
.topbar .left{left:162px;top:0}
.topbar .right{left:860px;top:0}
.sep{display:inline-block;width:1px;height:15px;background:var(--white);vertical-align:middle;margin:0 4px}

.header{left:0;top:30px;width:1200px;height:83px}
.brand{left:162px;top:26px;display:flex;align-items:center;gap:14px}
.brand-dot{width:30px;height:30px;border-radius:50%;background:var(--blue)}
.brand-name{font-family:"Raleway",sans-serif;font-weight:600;font-size:21px;color:var(--ink)}
.nav a{position:absolute;top:0;height:83px;line-height:83px;font-size:11px;color:var(--text)}
.nav .active{background:var(--blue-dark);color:var(--white);text-align:center;width:60px}

.crumbs{left:0;top:113px;width:1200px;height:59px;background:var(--band)}
.crumbs .title{left:162px;top:15px;font-size:10.5px;font-weight:700;color:var(--ink)}
.crumbs .path{left:162px;top:34px;font-size:10px;color:var(--ink)}

.col-head{font-size:11px;font-weight:700;color:var(--ink);padding-bottom:6px;border-bottom:1px solid var(--rule)}
.links-list{list-style:none;font-size:10px}
.links-list li{height:22.5px;position:relative;padding-left:15px}
.links-list li svg{position:absolute;left:0;top:4px}
.links-list .current{color:var(--blue);font-weight:600}

.panel{border:1px solid #cfcfcf}
.panel-head{height:33px;background:var(--blue);color:var(--white);font-size:11px;font-weight:700;line-height:33px;padding-left:13px}
.panel-body{padding:11px 13px;font-size:10px;line-height:14.5px}
.field-label{font-size:10px;font-weight:600;color:var(--ink);margin-top:14px}
.field{height:30px;border:1px solid #e2e2e2;background:#fafafa;margin-top:6px;font-size:9px;line-height:28px;padding-left:13px;color:#555;position:relative}
.field svg{position:absolute;right:12px;top:12px}
.submit{width:128px;height:30px;background:var(--blue);color:var(--white);font-size:11px;font-weight:700;text-align:center;line-height:30px;border-radius:2px;margin-top:14px}

.post{left:386px;width:430px}
.date{position:absolute;left:0;top:3px;width:53px;height:46px;background:var(--blue-dark);color:var(--white);text-align:center;font-weight:700;font-size:14.5px;line-height:17px;padding-top:4px}
.date sup{font-size:8px}
.post h3{margin-left:75px;font-size:12.5px;line-height:17px;font-weight:700;color:var(--ink)}
.post h3.current{color:var(--blue)}
.post p{margin-left:75px;margin-top:6px;font-size:9.5px;line-height:15px;color:var(--ink)}

.hours{width:100%;font-size:10px;border-collapse:collapse;margin-top:12px}
.hours td{height:18px}
.hours td:last-child{text-align:right}
.divider{height:1px;background:#cfcfcf;margin:18px 0 16px}
.sub-head{font-size:10.5px;font-weight:700;color:var(--ink);margin-bottom:6px}
.contact{font-size:10px;line-height:15px;display:grid;grid-template-columns:94px 1fr}

.footer-rule{left:0;top:808px;width:1200px;height:4px;background:var(--blue)}
.footer{left:0;top:812px;width:1200px;height:223px;background:var(--footer);color:var(--footer-text)}
.footer .brand-name{color:var(--white)}
.footer .brand-dot{background:var(--white)}
.f-about{left:162px;top:85px;width:205px;font-size:9px;line-height:13px;color:#ddd}
.f-col h4{font-size:12.5px;font-weight:600;color:var(--footer-head);margin-bottom:8px}
.f-col a{display:block;font-size:9.5px;height:18px}
.f-col a.current{color:#eee}
.f-contact{font-size:9.5px;line-height:15px;display:grid;grid-template-columns:90px 1fr}
.f-bottom-rule{left:0;top:188px;width:1200px;height:1px;background:#444}
.f-bottom{top:198px;font-size:9.5px}
</style>
</head>
<body>

<div class="abs topbar">
  <div class="abs left">To help Here : 555 014 2200 <span class="sep"></span> Email : hello@ Northpine.ca</div>
  <div class="abs right">Book an Appointment <span class="sep"></span> Physician Toolbox</div>
</div>

<header class="abs header">
  <div class="abs brand"><span class="brand-dot"></span><span class="brand-name">Medical Clinics</span></div>
  <nav class="nav">
    <a style="left:571px">Home</a>
    <a style="left:639px">Our Clinic</a>
    <a style="left:726px">Our Staff</a>
    <a class="active" style="left:803px">Resources</a>
    <a style="left:897px">Alerts</a>
    <a style="left:964px">Contact Us</a>
  </nav>
</header>

<section class="abs crumbs">
  <div class="abs title">RESOURCES</div>
  <div class="abs path">HOME / RESOURCES</div>
</section>

<aside class="abs" style="left:162px;top:219px;width:202px">
  <div class="col-head">RESOURCES LINKS</div>
  <ul class="links-list" style="margin-top:20px">
    <li class="current"><svg width="6" height="8" viewBox="0 0 6 8"><path d="M1 1l3 3-3 3" stroke="currentColor" fill="none" stroke-width="1.3"/></svg>Local Services</li>
    <li><svg width="6" height="8" viewBox="0 0 6 8"><path d="M1 1l3 3-3 3" stroke="#222" fill="none" stroke-width="1.3"/></svg>RDA and Drug Coverage</li>
    <li><svg width="6" height="8" viewBox="0 0 6 8"><path d="M1 1l3 3-3 3" stroke="#222" fill="none" stroke-width="1.3"/></svg>Mental Health Resources</li>
  </ul>
</aside>

<aside class="abs panel" style="left:161px;top:407px;width:203px;height:240px">
  <div class="panel-head">RESOURCE FORM</div>
  <div class="panel-body">
    Lorem Ipsum is simply dummy text of the printing and typesetting
    <div class="field-label">Title:</div>
    <div class="field"></div>
    <div class="field-label" style="margin-top:7px">Category:</div>
    <div class="field">Select Category:<svg width="8" height="5" viewBox="0 0 8 5"><path d="M1 1l3 3 3-3" stroke="#555" fill="none"/></svg></div>
    <div class="submit">Submit</div>
  </div>
</aside>

<div class="abs" style="left:386px;top:219px;width:428px"><div class="col-head">PATIENT HEALTH</div></div>

<article class="abs post" style="top:256px">
  <div class="date">June<br>25<sup>th</sup></div>
  <h3 class="current">Lorem Ipsum is simply dummy text of the printing and typesetting industry.</h3>
  <p>Contrary to popular belief, Lorem Ipsum is not simply random text. It has roots in a piece of classical Latin literature from 45 BC, making it over 2000 years old. Ona Verlaine,</p>
</article>
<article class="abs post" style="top:358px">
  <div class="date">June<br>24<sup>th</sup></div>
  <h3>Lorem Ipsum is simply dummy text of the printing and typesetting industry.</h3>
  <p>Contrary to popular belief, Lorem Ipsum is not simply random text. It has roots in a piece of classical Latin literature from 45 BC, making it over 2000 years old. Ona Verlaine,</p>
</article>
<article class="abs post" style="top:459px">
  <div class="date">June<br>23<sup>th</sup></div>
  <h3>Lorem Ipsum is simply dummy text of the printing and typesetting industry.</h3>
  <p>Contrary to popular belief, Lorem Ipsum is not simply random text. It has roots in a piece of classical Latin literature from 45 BC, making it over 2000 years old. Ona Verlaine,</p>
</article>
<article class="abs post" style="top:559px">
  <div class="date">June<br>22<sup>th</sup></div>
  <h3>Lorem Ipsum is simply dummy text of the printing and typesetting industry.</h3>
  <p>Contrary to popular belief, Lorem Ipsum is not simply random text. It has roots in a piece of classical Latin literature from 45 BC, making it over 2000 years old. Ona Verlaine,</p>
</article>
<article class="abs post" style="top:660px">
  <div class="date">June<br>22<sup>th</sup></div>
  <h3>Lorem Ipsum is simply dummy text of the printing and typesetting industry.</h3>
  <p>Contrary to popular belief, Lorem Ipsum is not simply random text. It has roots in a piece of classical Latin literature from 45 BC, making it over 2000 years old. Ona Verlaine,</p>
</article>

<aside class="abs panel" style="left:836px;top:209px;width:203px;height:360px">
  <div class="panel-head">HOURS OF OPRATION</div>
  <div class="panel-body" style="padding-top:8px">
    Lorem Ipsum is simply dummy text of the printing and typesetting
    <table class="hours">
      <tr><td>Monday :</td><td>8:00 AM - 6:00 PM</td></tr>
      <tr><td>Tuesday :</td><td>8:00 AM - 6:00 PM</td></tr>
      <tr><td>Wednesday :</td><td>8:00 AM - 6:00 PM</td></tr>
      <tr><td>Thursday :</td><td>8:00 AM - 6:00 PM</td></tr>
      <tr><td>Friday :</td><td>8:00 AM - 6:00 PM</td></tr>
      <tr><td>Saturday :</td><td>9:00 AM - 4:00 PM</td></tr>
      <tr><td>Sunday :</td><td>9:00 AM - 4:00 PM</td></tr>
    </table>
    <div class="divider"></div>
    <div class="sub-head">CONTACT INFO</div>
    <div class="contact">
      <span>Telephone :</span><span>555-013-4477</span>
      <span>Email:</span><span>hello@northpine.ca</span>
      <span>Address:</span><span>48 Alder Row<br>Fernhollow,<br>Q1Z 7XK</span>
    </div>
  </div>
</aside>

<div class="abs footer-rule"></div>
<footer class="abs footer">
  <div class="abs brand" style="top:38px"><span class="brand-dot"></span><span class="brand-name">Medical Clinics</span></div>
  <p class="abs f-about">Lorem Ipsum is simply dummy text of the printing and typesetting industry. Lorem Ipsum has been the industry's standard dummy text</p>
  <div class="abs f-col" style="left:461px;top:32px">
    <h4>Navigation</h4>
    <a class="current">Home</a><a>Our Clinic</a><a>Newsletter</a><a>Our Staff</a><a>Resources</a>
  </div>
  <div class="abs f-col" style="left:686px;top:32px">
    <h4>Links</h4>
    <a>Help</a><a>Support</a><a>Privacy Policy</a>
  </div>
  <div class="abs f-col" style="left:836px;top:31px;width:200px">
    <h4>Contact Us</h4>
    <div class="f-contact">
      <span>Telephone :</span><span>555-013-4477</span>
      <span>Email:</span><span>hello@northpine.ca</span>
      <span>Address:</span><span>48 Alder Row<br>Fernhollow,<br>Q1Z 7XK</span>
    </div>
  </div>
  <div class="abs f-bottom-rule"></div>
  <div class="abs f-bottom" style="left:162px">© 2015 Medical Clinces. All Rights Reservsd</div>
  <div class="abs f-bottom" style="left:461px">About Us</div>
  <div class="abs f-bottom" style="left:530px">Terms of Use</div>
  <div class="abs f-bottom" style="left:615px">Privacy Policy</div>
</footer>

</body>
</html>
```